Vellmore Family Law, legal technician needs a website and design

I need a website for a family law practice. I specialize in collaborative law, unbundled services, and mediation. The website must contain my company logo (file attached), and the website must be a mixture of my personality and my profession. I have attached additional information to explain my personality and profession.

Target Market(s)

Lower through middle-class (income level up to $200,000 per year)

Coding

Coded - Design and coding required

Number of Pages Required

1 page

Requirements
Must have
• Must have enough pages to cover required content. I submitted below some content about the collaborative law process. All of the content is not necessary. However, the website must have enough content to clearly describe the services I offer. Use your professionalism and judgment regarding font, font size, etc.

```html
<!DOCTYPE html>
<html lang="en">
<head>
<meta charset="utf-8">
<title>Vellmore Family Law</title>
<link rel="stylesheet" href="https://fonts.googleapis.com/css2?family=Cinzel:wght@400;700&family=Open+Sans:wght@400;600;700&display=swap">
<style>
:root{
  --navy:#0a0d2b;
  --olive:#857a32;
  --ink:#14172e;
  --text:#666a75;
  --white:#ffffff;
  --card-shadow:0 6px 22px rgba(0,0,0,.12);
}
*{margin:0;padding:0;box-sizing:border-box}
html,body{width:1200px;height:3139px;overflow:hidden}
body{position:relative;background:var(--white);font-family:"Open Sans",Arial,sans-serif;color:var(--text)}
.abs{position:absolute}
.btn{position:absolute;display:flex;align-items:center;justify-content:center;background:var(--olive);color:var(--white);font-weight:700;text-transform:uppercase;letter-spacing:.3px;white-space:nowrap}
.photo{position:absolute}

/* header */
.site-header{left:0;top:0;width:1200px;height:88px;background:var(--navy)}
.brand{position:absolute;display:flex;align-items:center;gap:12px}
.brand-dot{width:14px;height:14px;border-radius:50%;background:var(--olive);flex:none}
.brand-name{font-family:"Open Sans",Arial,sans-serif;font-weight:600;color:var(--olive);text-transform:uppercase;letter-spacing:1px}
.header-brand{left:144px;top:30px}
.header-brand .brand-name{font-size:20px;white-space:nowrap}
.main-nav{left:454px;top:30px;height:28px;border-left:3px solid var(--olive);display:flex;align-items:center}
.main-nav a{color:var(--white);text-decoration:none;font-size:13px;font-weight:600;margin-left:12px;margin-right:18px}
.phone-btn{left:871px;top:28px;width:184px;height:32px;font-size:18px;gap:8px}

/* hero */
.hero{left:0;top:88px;width:1200px;height:537px;background:linear-gradient(90deg,#c9a79a 0%,#5d6470 25%,#3b4150 50%,#6d7480 75%,#8c8f98 100%)}
.hero-title{left:0;top:236px;width:1200px;text-align:center;font-family:"Cinzel",serif;font-weight:700;font-size:64px;color:var(--white);text-shadow:2px 3px 4px rgba(0,0,0,.5)}
.hero-title span{color:var(--olive)}
.hero-sub{left:0;top:338px;width:1200px;text-align:center;font-size:27px;font-weight:600;color:var(--white);text-shadow:1px 2px 3px rgba(0,0,0,.5)}
.hero-btn{left:532px;top:406px;width:135px;height:30px;font-size:15px}
.slider-dots{left:1130px;top:303px;display:flex;flex-direction:column;gap:10px}
.slider-dots i{width:9px;height:9px;border-radius:50%;background:var(--white)}
.slider-dots i.on{background:var(--olive)}

/* service cards */
.card{position:absolute;background:var(--white);box-shadow:var(--card-shadow);text-align:center}
.card h3{font-size:15px;font-weight:700;color:var(--ink);margin-bottom:14px}
.card p{font-size:12px;line-height:21px;color:var(--text);padding:0 22px}
.card .photo{position:relative;margin:16px auto 0}
.card .btn{position:relative;margin:0 auto}
.card-side{top:502px;width:293px;height:366px}
.card-side .photo{width:263px;height:150px;margin-bottom:25px}
.card-side .btn{width:136px;height:31px;font-size:15px;margin-top:22px}
.card-main{left:437px;top:502px;width:325px;height:404px;z-index:2}
.card-main .photo{width:290px;height:166px;margin-bottom:28px}
.card-main h3{font-size:17px}
.card-main p{font-size:13.5px;line-height:23px}
.card-main .btn{width:150px;height:34px;font-size:17px;margin-top:26px}

/* about */
.about-title{left:144px;top:1020px;font-family:"Cinzel",serif;font-size:50px;color:var(--navy)}
.about-sub{left:147px;top:1086px;font-family:"Cinzel",serif;font-size:38px;color:var(--olive);letter-spacing:1px;white-space:nowrap}
.about-text{left:144px;top:1150px;width:452px;font-size:13px;line-height:24px}
.about-btn{left:144px;top:1376px;width:150px;height:36px;font-size:17px}
.about-seal{left:643px;top:1037px;width:370px;height:370px;border:5px solid var(--olive);border-radius:50%;display:flex;align-items:center;justify-content:center}
.about-seal .brand-name{font-size:30px;text-align:center;line-height:40px}

/* video */
.video{left:18px;top:1514px;width:955px;height:471px;background:linear-gradient(120deg,#2b3244,#4a4c55 40%,#3a3f4e 70%,#1d2233)}
.play-icon{left:450px;top:1703px}
.olive-block-a{left:991px;top:1820px;width:209px;height:303px;background:var(--olive)}
.olive-block-b{left:895px;top:2001px;width:305px;height:122px;background:var(--olive)}

/* articles */
.articles-title{left:0;top:2095px;width:1200px;text-align:center;font-family:"Cinzel",serif;font-size:50px;color:var(--navy)}
.articles-title span{color:var(--olive)}
.meta{font-size:13px;color:var(--olive)}
.feature-img{left:145px;top:2213px;width:457px;height:241px;background:linear-gradient(180deg,#d7dce4,#a9aebb 60%,#8c8378)}
.feature-meta{left:145px;top:2487px}
.feature-title{left:145px;top:2529px;font-size:18px;font-weight:700;color:var(--ink);white-space:nowrap}
.feature-text{left:145px;top:2571px;width:440px;font-size:15px;line-height:26px}
.feature-btn{left:145px;top:2673px;width:167px;height:38px;font-size:19px}
.post-img{left:641px;width:198px;height:153px}
.post-meta{left:867px}
.post-title{left:867px;width:220px;font-size:18px;font-weight:700;line-height:27px;color:var(--ink)}

/* contact band */
.contact-band{left:0;top:2800px;width:1200px;height:133px;background:var(--navy)}
.contact-title{left:144px;top:2842px;font-size:38px;font-weight:700;color:var(--white);white-space:nowrap}
.contact-title span{color:var(--olive)}
.email-btn{left:890px;top:2848px;width:166px;height:37px;font-size:19px;gap:12px}

/* footer */
.footer-brand{left:152px;top:3008px}
.footer-brand .brand-name{font-size:26px;line-height:32px}
.contact-btn{left:515px;top:2970px;width:167px;height:38px;font-size:19px}
.footer-phone{left:706px;top:2975px;font-size:19px;font-weight:700;color:var(--navy);display:flex;align-items:center;gap:8px}
.footer-nav{left:515px;top:3033px;font-size:18px;font-weight:700;color:var(--navy);white-space:nowrap}
.footer-nav b{margin:0 16px;font-weight:600}
.copyright{left:515px;top:3078px;font-size:12.5px;color:var(--ink);white-space:nowrap}
</style>
</head>
<body>

<header class="abs site-header">
  <div class="brand header-brand"><span class="brand-dot"></span><span class="brand-name">Vellmore Family Law</span></div>
  <nav class="abs main-nav"><a>HOME</a><a>ABOUT</a><a>SERVICES</a><a>ARTICLES</a><a>CONTACT</a></nav>
  <div class="btn phone-btn">
    <svg width="18" height="18" viewBox="0 0 24 24"><path fill="#fff" d="M6.6 10.8a15.1 15.1 0 006.6 6.6l2.2-2.2a1 1 0 011-.25 11.4 11.4 0 003.6.57 1 1 0 011 1V20a1 1 0 01-1 1A17 17 0 013 4a1 1 0 011-1h3.5a1 1 0 011 1c0 1.250.2 2.450.57 3.57a1 1 0 01-.25 1z"/></svg>
    1 800 555 0142
  </div>
</header>

<section class="abs hero" role="img" aria-label="Photo of a family meeting with a lawyer in an office"></section>
<h1 class="abs hero-title">VELLMORE <span>FAMILY LAW</span></h1>
<p class="abs hero-sub">We are a family law practice</p>
<div class="btn hero-btn">Get Started</div>
<div class="abs slider-dots"><i></i><i></i><i class="on"></i><i></i><i></i></div>

<article class="card card-side" style="left:145px">
  <div class="photo" role="img" aria-label="Photo of a team reviewing papers around a table" style="background:linear-gradient(135deg,#8c6a48,#c7a57c 50%,#6e7c92)"></div>
  <h3>COLLABORATIVE LAW</h3>
  <p>Lorem ipsum dolor sit amet, consectetur adipiscing ed do eiusmod tempor incididunt ut labore et dolore magna aliqua.</p>
  <div class="btn">Read More</div>
</article>
<article class="card card-main">
  <div class="photo" role="img" aria-label="Photo of a hand signing a document" style="background:linear-gradient(135deg,#c8ccd3,#a48b73 50%,#e6e7ea)"></div>
  <h3>UNBUNDLED SERVICES</h3>
  <p>Lorem ipsum dolor sit amet, consectetur adipiscing ed do eiusmod tempor incididunt ut labore et dolore magna aliqua.</p>
  <div class="btn">Read More</div>
</article>
<article class="card card-side" style="left:762px">
  <div class="photo" role="img" aria-label="Photo of two people shaking hands across a desk" style="background:linear-gradient(135deg,#dfe4e8,#6c6f78 50%,#2d2f36)"></div>
  <h3>MEDIATION</h3>
  <p>Lorem ipsum dolor sit amet, consectetur adipiscing ed do eiusmod tempor incididunt ut labore et dolore magna aliqua.</p>
  <div class="btn">Read More</div>
</article>

<h2 class="abs about-title">ABOUT</h2>
<p class="abs about-sub">VELLMORE FAMILY LAW</p>
<p class="abs about-text">Lorem ipsum dolor sit amet, consectetur adipiscing elit, sed do eiusmod tempor incididunt ut labore et dolore magna aliqua.uis ipsum suspendisse ultrices gravida. Risus commodo viverra maecenas accumsan lacus vel facilisis. Lorem ipsum dolor sit amet, consectetur adipiscing elit, sed do eiusmod tempor incididunt ut labore et dolore magna aliqua.uis ipsum suspendisse ultrices gravida. Risus commodo viverra maecenas accumsan lacus vel facilisis. Lorem ipsum dolor sit amet, consectetur adipiscing elit, sed do eiusmod tempor incididunt ut labore et dolore</p>
<div class="btn about-btn">Read More</div>
<div class="abs about-seal"><span class="brand-name">Vellmore<br>Family Law</span></div>

<div class="abs olive-block-a"></div>
<div class="abs olive-block-b"></div>
<div class="abs video" role="img" aria-label="Video still of a mother and daughter meeting a lawyer at a desk"></div>
<svg class="abs play-icon" width="92" height="92" viewBox="0 0 92 92" aria-label="Play video">
  <circle cx="46" cy="46" r="42" fill="none" stroke="#fff" stroke-width="5"/>
  <path d="M38 30 L62 46 L38 62 Z" fill="#fff"/>
</svg>

<h2 class="abs articles-title">FEATURED <span>ARTICLES</span></h2>

<div class="abs feature-img" role="img" aria-label="Photo of a couple meeting a mediator at a table"></div>
<p class="abs meta feature-meta">June 18,2021 &nbsp;| &nbsp;Comments</p>
<h3 class="abs feature-title">SED UT PERSPICIATIS UNDE OMNIS ISTERROR</h3>
<p class="abs feature-text">Lorem ipsum dolor sit amet, consectetur adipiscing ed do eiusmod tempor incididunt ut labore et dolore magna aliqua. Quis ipsum suspendisse ultrices gravida.</p>
<div class="btn feature-btn">Read More</div>

<div class="abs post-img" style="top:2213px;background:linear-gradient(135deg,#6b4a3b,#c9b9ad 55%,#8a96ab)" role="img" aria-label="Photo of a mother and daughter"></div>
<p class="abs meta post-meta" style="top:2232px">June 18,2021 &nbsp;| &nbsp;Comments</p>
<h3 class="abs post-title" style="top:2269px">SED UT PERSPICIATIS UNDE OMNIS ISTER CUSANTIROR</h3>

<div class="abs post-img" style="top:2386px;background:linear-gradient(135deg,#2a2522,#5a4a3e 50%,#d8d4cf)" role="img" aria-label="Photo of a person signing papers"></div>
<p class="abs meta post-meta" style="top:2405px">June 18,2021 &nbsp;| &nbsp;Comments</p>
<h3 class="abs post-title" style="top:2442px">SED UT PERSPICIATIS UNDE OMNIS ISTER CUSANTIROR</h3>

<div class="abs post-img" style="top:2559px;background:linear-gradient(135deg,#5a3a26,#2b2f3c 55%,#8a6a4a)" role="img" aria-label="Photo of hands holding a law book"></div>
<p class="abs meta post-meta" style="top:2578px">June 18,2021 &nbsp;| &nbsp;Comments</p>
<h3 class="abs post-title" style="top:2615px">SED UT PERSPICIATIS UNDE OMNIS ISTER CUSANTIROR</h3>

<section class="abs contact-band"></section>
<h2 class="abs contact-title"><span>CONTACT</span> VELLMORE FAMILY LAW</h2>
<div class="btn email-btn">
  <svg width="20" height="15" viewBox="0 0 20 15"><rect x="0" y="0" width="20" height="15" rx="2" fill="#fff"/><path d="M1 1.5 L10 8.5 L19 1.5" fill="none" stroke="#857a32" stroke-width="1.8"/></svg>
  Email Me
</div>

<footer>
  <div class="brand footer-brand"><span class="brand-dot"></span><span class="brand-name">Vellmore<br>Family Law</span></div>
  <div class="btn contact-btn">Contact Me</div>
  <div class="abs footer-phone">
    <svg width="18" height="18" viewBox="0 0 24 24"><path fill="#0a0d2b" d="M6.6 10.8a15.1 15.1 0 006.6 6.6l2.2-2.2a1 1 0 011-.25 11.4 11.4 0 003.6.57 1 1 0 011 1V20a1 1 0 01-1 1A17 17 0 013 4a1 1 0 011-1h3.5a1 1 0 011 1c0 1.250.2 2.450.57 3.57a1 1 0 01-.25 1z"/></svg>
    1 800 555 0142
  </div>
  <nav class="abs footer-nav">HOME<b>/</b>ABOUT<b>/</b>SERVICES<b>/</b>ARTICLES<b>/</b>CONTACT</nav>
  <p class="abs copyright">© 2021 Vellmore Family Law. All rights reserved.Privacy Terms of Use</p>
</footer>

</body>
</html>
```